Beautify our counselling web application

I have a web application in development and at the moment it is very plain.
It has being developed with laravel and vue. I need a simple design for the user interface to make it look more sleek and professional. I will need someone who is able to code the design as part of the service. The app is very low-cost for voluntary and social enterprise services and we don't have a lot of money so I need someone who is just starting out or someone with a big heart.
I have uploaded current pages to show the contents.
I will tip for good work.

Target Market(s)

Counsellors and psychotherapists

Industry/Entity Type

SaaS

Font styles to use
Serif
Sans Serif

Colors
0054AA
0677BA
7BADD7
CADEEF
E8F1F8

Requirements
Must have
• Ability to code the design into the current site
Nice to have
• elegant, modern. cool, profession. nice examples include merovaultix.com quillbanter.com fenrodu.com
Should not have
• corny literal 90s icons, icons with more than one colour using primary colours

```html
<!DOCTYPE html>
<html lang="en">
<head>
<meta charset="utf-8">
<title>Counselling App – Interface Screens</title>
<link href="https://fonts.googleapis.com/css2?family=Montserrat:wght@400;500;600;700;800&display=swap" rel="stylesheet">
<style>
  :root{
    --stage:#848484;
    --sidebar:#0f5a93;
    --nav-active:#0677BA;
    --primary:#0054AA;
    --tab-dark:#0f5a93;
    --panel:#f1f1f1;
    --white:#ffffff;
    --ink:#111111;
    --muted:#9aa9bb;
    --ok:#22a83a;
    --alert:#9b1020;
    --row-shadow:rgba(0,0,0,.08);
  }
  *{box-sizing:border-box;margin:0;padding:0}
  html,body{width:808px;height:1200px;overflow:hidden}
  body{background:var(--stage);font-family:'Montserrat',sans-serif;color:var(--ink);position:relative}

  .screen{position:absolute;left:37px;width:734px;height:346px;background:var(--white);overflow:hidden}
  .screen--dashboard{top:45px}
  .screen--caseload{top:427px}
  .screen--client{top:809px}

  .sidebar{position:absolute;left:0;top:0;width:90px;height:100%;background:var(--sidebar)}
  .sidebar__brand{position:absolute;left:9px;top:13px;color:var(--white);font-weight:700;font-size:7.4px;letter-spacing:.1px;white-space:nowrap}
  .sidebar__nav{position:absolute;left:0;top:31px;list-style:none}
  .sidebar__item{height:13.1px;width:66px;padding-left:11px;color:var(--white);font-weight:700;font-size:4.3px;line-height:13.1px;letter-spacing:.1px;border-radius:0 7px 7px 0}
  .sidebar__item--active{background:var(--nav-active)}

  .toolbar{position:absolute;top:14px;display:flex;gap:5px}
  .toolbar svg{width:7px;height:7px;fill:var(--tab-dark)}

  .welcome{position:absolute;left:113px;top:35px;width:591px;height:290px;background:var(--panel);border-radius:3px}
  .welcome__title{position:absolute;left:0;right:0;top:75px;text-align:center;font-weight:800;font-size:25.5px;letter-spacing:.6px}
  .welcome__subtitle{position:absolute;left:0;right:0;top:119px;text-align:center;font-weight:600;font-size:10.5px}
  .btn-create{position:absolute;left:234px;top:145px;width:120px;height:23px;background:var(--primary);color:var(--white);border-radius:2px;font-weight:600;font-size:7.6px;display:flex;align-items:center;justify-content:center}
  .summary-tabs{position:absolute;left:201px;top:200px;width:188px;height:30px;display:flex;border-radius:3px;overflow:hidden;box-shadow:0 2px 6px rgba(0,0,0,.12)}
  .summary-tab{flex:0 0 95px;display:flex;flex-direction:column;align-items:center;justify-content:center;background:var(--white);color:var(--primary)}
  .summary-tab--active{flex:1;background:var(--primary);color:var(--white)}
  .summary-tab__label{font-weight:600;font-size:7.8px}
  .summary-tab__note{font-weight:600;font-size:4.3px;margin-top:2px}

  .page-title{position:absolute;font-weight:600;font-size:10px;white-space:nowrap}
  .search{position:absolute;left:114px;top:37px;width:166px;height:15px;background:var(--white);border-radius:8px;box-shadow:0 1px 5px rgba(0,0,0,.1);display:flex;align-items:center;padding-left:11px;font-size:4.8px}
  .search__filter{color:#333;margin-right:9px}
  .search__filter::after{content:"";display:inline-block;margin-left:3px;border:1.5px solid transparent;border-top:2px solid #333;vertical-align:middle}
  .search__input{color:#aaa}
  .col-head{position:absolute;top:74px;font-weight:600;font-size:6.6px;white-space:nowrap}
  .row{position:absolute;left:113px;width:599px;height:29px;background:var(--white);border-radius:3px;box-shadow:0 1px 5px var(--row-shadow)}
  .cell{position:absolute;top:0;line-height:29px;font-size:5.5px;white-space:nowrap}
  .cell--risk{left:12px;top:11px;width:6px;height:6px}
  .contacts-btn{position:absolute;left:561px;top:7px;width:32px;height:15px;background:var(--primary);color:var(--white);border-radius:2px;font-weight:600;font-size:5.3px;display:flex;align-items:center;justify-content:center}

  .client-tab{position:absolute;top:44px;height:22px;border-radius:2px;font-weight:600;font-size:6.8px;display:flex;align-items:center;justify-content:center;white-space:nowrap}
  .client-tab--solid{background:var(--tab-dark);color:var(--white)}
  .client-tab--outline{border:1px solid var(--tab-dark);color:var(--tab-dark);background:var(--white)}
  .client-tab--disabled{border:1px solid #a9bfd6;color:var(--muted);background:var(--white)}
  .episode{position:absolute;left:106px;top:79px;width:597px;height:128px;background:var(--white);border-radius:3px;box-shadow:0 1px 8px rgba(0,0,0,.09)}
  .episode__name{position:absolute;left:24px;top:15px;font-weight:600;font-size:6.6px}
  .episode__start{position:absolute;left:438px;top:10px;font-weight:600;font-size:6.6px;white-space:nowrap}
  .badge-note{position:absolute;left:536px;top:9px;width:42px;height:11px;background:var(--alert);color:var(--white);border-radius:2px;font-weight:700;font-size:3.2px;display:flex;align-items:center;justify-content:center}
  .record-btn{position:absolute;height:19px;background:var(--tab-dark);color:var(--white);border-radius:2px;font-weight:700;font-size:5.5px;display:flex;align-items:center;justify-content:center;white-space:nowrap}
</style>
</head>
<body>

<svg width="0" height="0" style="position:absolute">
  <defs>
    <symbol id="i-help" viewBox="0 0 16 16"><path d="M8 0a8 8 0 1 0 0 16A8 8 0 0 0 8 0zm.9 12.6H7.1v-1.8h1.8v1.8zm1.9-5.9c-.4.5-.8.8-1.2 1.1-.5.3-.7.6-.7 1.3H7.1c0-1.2.4-1.8 1.1-2.3.5-.3.9-.6.9-1.2 0-.5-.4-.9-1.1-.9-.7 0-1.100.4-1.2 1.1H5c.1-1.7 1.3-2.6 3-2.6s3 .9 3 2.3c0 .5-.1.9-.2 1.2z"/></symbol>
    <symbol id="i-user" viewBox="0 0 16 16"><circle cx="8" cy="4.5" r="3.7"/><path d="M1.5 16c0-4 2.8-6.6 6.5-6.6s6.5 2.6 6.5 6.6z"/></symbol>
    <symbol id="i-out" viewBox="0 0 16 16"><path d="M6 2H2v12h4v-2H4V4h2z"/><path d="M10 3.5 15 8l-5 4.5V10H6V6h4z"/></symbol>
    <symbol id="i-ok" viewBox="0 0 16 16"><circle cx="8" cy="8" r="8" fill="#22a83a"/><path d="M4.3 8.2 7 10.8l4.8-5" fill="none" stroke="#fff" stroke-width="2.2"/></symbol>
  </defs>
</svg>

<section class="screen screen--dashboard">
  <aside class="sidebar">
    <div class="sidebar__brand">COUNSELLING APP</div>
    <ul class="sidebar__nav">
      <li class="sidebar__item sidebar__item--active">DASHBOARD</li>
      <li class="sidebar__item">CASELOAD</li>
      <li class="sidebar__item">CALENDAR</li>
      <li class="sidebar__item">ADDRESS BOOK</li>
      <li class="sidebar__item">USERS</li>
      <li class="sidebar__item">SERVICES</li>
      <li class="sidebar__item">CLIENTS</li>
      <li class="sidebar__item">AUDIT</li>
      <li class="sidebar__item">MONITORING</li>
    </ul>
  </aside>
  <div class="toolbar" style="left:671px"><svg><use href="#i-help"/></svg><svg><use href="#i-user"/></svg><svg><use href="#i-out"/></svg></div>
  <div class="welcome">
    <h1 class="welcome__title">WELOCME TO</h1>
    <h2 class="welcome__subtitle">NOTIFICATIONS</h2>
    <div class="btn-create">CREATE NOTIFICATION</div>
    <div class="summary-tabs">
      <div class="summary-tab"><span class="summary-tab__label">TODAY</span><span class="summary-tab__note">NO APPOINTMENTST</span></div>
      <div class="summary-tab summary-tab--active"><span class="summary-tab__label">REVIEWS</span><span class="summary-tab__note">NO REVIEWS</span></div>
    </div>
  </div>
</section>

<section class="screen screen--caseload">
  <aside class="sidebar">
    <div class="sidebar__brand">COUNSELLING APP</div>
    <ul class="sidebar__nav">
      <li class="sidebar__item">DASHBOARD</li>
      <li class="sidebar__item sidebar__item--active">CASELOAD</li>
      <li class="sidebar__item">CALENDAR</li>
      <li class="sidebar__item">ADDRESS BOOK</li>
      <li class="sidebar__item">USERS</li>
      <li class="sidebar__item">SERVICES</li>
      <li class="sidebar__item">CLIENTS</li>
      <li class="sidebar__item">AUDIT</li>
      <li class="sidebar__item">MONITORING</li>
    </ul>
  </aside>
  <h1 class="page-title" style="left:115px;top:12px">Caseload</h1>
  <div class="toolbar" style="left:486px;top:13px"><svg><use href="#i-help"/></svg><svg><use href="#i-user"/></svg><svg><use href="#i-out"/></svg></div>
  <div class="search"><span class="search__filter">Filter</span><span class="search__input">Search...</span></div>

  <span class="col-head" style="left:118px">Risk</span>
  <span class="col-head" style="left:151px">Alerts</span>
  <span class="col-head" style="left:198px">Client</span>
  <span class="col-head" style="left:291px">ID</span>
  <span class="col-head" style="left:337px">Service</span>
  <span class="col-head" style="left:413px">Therapist</span>
  <span class="col-head" style="left:468px">Date of referral</span>
  <span class="col-head" style="left:538px">First Contact</span>
  <span class="col-head" style="left:602px">Previous Episode</span>
  <span class="col-head" style="left:676px">Contacts</span>

  <div class="row" style="top:99px"><svg class="cell cell--risk"><use href="#i-ok"/></svg><span class="cell" style="left:86px">Milo Farrant</span><span class="cell" style="left:178px">002</span><span class="cell" style="left:225px">Demo Service 1</span><span class="cell" style="left:301px">Owen</span><span class="cell" style="left:357px">05/07/2022</span><span class="cell" style="left:426px">20/09/2022</span><span class="contacts-btn">Total: 3</span></div>
  <div class="row" style="top:135px"><svg class="cell cell--risk"><use href="#i-ok"/></svg><span class="cell" style="left:86px">Ansel Corbitt</span><span class="cell" style="left:178px">002</span><span class="cell" style="left:225px">Demo Service 1</span><span class="cell" style="left:301px">Owen</span><span class="cell" style="left:357px">05/07/2022</span><span class="cell" style="left:426px">20/09/2022</span><span class="contacts-btn">Total: 2</span></div>
  <div class="row" style="top:174px"><svg class="cell cell--risk"><use href="#i-ok"/></svg><span class="cell" style="left:86px">Tamsin Wrey</span><span class="cell" style="left:178px">002</span><span class="cell" style="left:225px">Demo Service 1</span><span class="cell" style="left:301px">Owen</span><span class="cell" style="left:357px">05/07/2022</span><span class="cell" style="left:426px">20/09/2022</span><span class="contacts-btn">Total: 3</span></div>
  <div class="row" style="top:210px"><svg class="cell cell--risk"><use href="#i-ok"/></svg><span class="cell" style="left:86px">Elsa Marrow</span><span class="cell" style="left:177px">002</span><span class="cell" style="left:224px">Demo Service 1</span><span class="cell" style="left:300px">Owen</span><span class="cell" style="left:356px">05/07/2022</span><span class="cell" style="left:425px">20/09/2022</span><span class="contacts-btn" style="left:560px">Total: 3</span></div>
  <div class="row" style="top:246px"><svg class="cell cell--risk"><use href="#i-ok"/></svg><span class="cell" style="left:86px">Imogen Castell</span><span class="cell" style="left:178px">002</span><span class="cell" style="left:225px">Demo Service 1</span><span class="cell" style="left:300px">Owen</span><span class="cell" style="left:356px">05/07/2022</span><span class="cell" style="left:425px">20/09/2022</span><span class="contacts-btn">Total: 0</span></div>
  <div class="row" style="top:283px"><svg class="cell cell--risk"><use href="#i-ok"/></svg><span class="cell" style="left:86px">Harriet Poldane</span><span class="cell" style="left:177px">002</span><span class="cell" style="left:224px">Demo Service 1</span><span class="cell" style="left:300px">Owen</span><span class="cell" style="left:356px">05/07/2022</span><span class="cell" style="left:425px">20/09/2022</span><span class="contacts-btn" style="left:560px">Total: 2</span></div>
</section>

<section class="screen screen--client">
  <aside class="sidebar">
    <div class="sidebar__brand">COUNSELLING APP</div>
    <ul class="sidebar__nav">
      <li class="sidebar__item">DASHBOARD</li>
      <li class="sidebar__item sidebar__item--active">CASELOAD</li>
      <li class="sidebar__item">CALENDAR</li>
      <li class="sidebar__item">ADDRESS BOOK</li>
      <li class="sidebar__item">USERS</li>
      <li class="sidebar__item">SERVICES</li>
      <li class="sidebar__item">CLIENTS</li>
      <li class="sidebar__item">AUDIT</li>
      <li class="sidebar__item">MONITORING</li>
    </ul>
  </aside>
  <h1 class="page-title" style="left:110px;top:11px">Caseload / &nbsp;Milo Farrant</h1>
  <div class="toolbar" style="left:671px"><svg><use href="#i-help"/></svg><svg><use href="#i-user"/></svg><svg><use href="#i-out"/></svg></div>

  <div class="client-tab client-tab--solid" style="left:109px;width:67px">Work Space</div>
  <div class="client-tab client-tab--solid" style="left:180px;width:92px">Client Information</div>
  <div class="client-tab client-tab--outline" style="left:276px;width:68px">Client Record</div>
  <div class="client-tab client-tab--outline" style="left:348px;width:82px">Client Progress</div>
  <div class="client-tab client-tab--disabled" style="left:435px;width:68px">Payments</div>

  <div class="episode">
    <div class="episode__name">Episode 01</div>
    <div class="episode__start">Started : Wed Sep 14 2022</div>
    <div class="badge-note">Non-clinical note</div>
    <div class="record-btn" style="left:23px;top:33px;width:56px">Session Record</div>
    <div class="record-btn" style="left:86px;top:33px;width:56px">Questionnaire</div>
    <div class="record-btn" style="left:148px;top:33px;width:56px">Document</div>
    <div class="record-btn" style="left:211px;top:33px;width:66px">Treatment Plan</div>
    <div class="record-btn" style="left:284px;top:33px;width:65px">Assessment</div>
    <div class="record-btn" style="left:356px;top:33px;width:66px">Risk mansgement</div>
    <div class="record-btn" style="left:428px;top:33px;width:66px">Non-clinical note</div>
    <div class="record-btn" style="left:23px;top:60px;width:56px">Summary</div>
    <div class="record-btn" style="left:86px;top:60px;width:56px">Safeguarding</div>
    <div class="record-btn" style="left:148px;top:60px;width:56px">Timeline</div>
    <div class="record-btn" style="left:211px;top:60px;width:57px">Consent</div>
  </div>
</section>

</body>
</html>
```